Graphic Design Project

We make rose petal jelly from old fashioned english roses. The jelly is sweet eaten with scones and clotted cream or as a filling in a victoria sandwich, as a topping on ice cream or thick set yogurt.
The image of the product is luxurious and decadent and very english.
We need a design for a label which has a picture of an old fashioned rose (rosa mundi or a compte de chambard) The rose must stand out clearly so the jelly is not confused with other fruit jams. The overall colour of the label should be pink and soft, with white or dark pink writing. The label needs to be fridge proof.

We also need a security strip to fit on the lid of the jar.

We need the following information on the label.
Name of our company-"Meadow Crown"
Name of Product-"Rose Petal Jelly"
Sales pitch-"With whole petals-a taste of summer, delicious on scones, as a filling in sponge cake, as a topping on ice cream or yogurt."
INGREDIENTS: Sugar, water, rose petals, lemon juice, natural jelling agent (agar-agar)
STORAGE: Store in a cool dry place, once opened keep refrigerated and consume within 4 weeks.
BEST BEFORE: See base

200g
Produced by:
MEADOW CROWN
The Larches
Pardew Lane
Ashcombe
Westmereshire
GL17 4RX
The label must have room for a bar code. The size of label approx 8-10cm long 5cm wide.
Updates

Hi

Just been looking at the Hartwell and Brace site and the labels they have there have the up market feel I am trying to convey. Hope that helps, its classy but not twee.

Thanks

Thanks for all submissions. I would be grateful if you googled images for 'Colourful and expensive biscuits at Hartwell Brace' The designs on the tins are the image we are trying to create. The colours are quite strong.

Thanks

Target Market(s)

older well off people who visit garden centres

Industry/Entity Type

Security

Requirements
Must have
• All writen info above and picture of old fashioned rose prferably rose a mundi. Luxury feel, very english, to appeal to older market
Pink colour sheme
Should not have
• dark or manly colours

```html
<!DOCTYPE html>
<html lang="en">
<head>
<meta charset="utf-8">
<title>Meadow Crown – Rose Petal Jelly label</title>
<link rel="stylesheet" href="https://fonts.googleapis.com/css2?family=Cinzel:wght@600&family=EB+Garamond:ital,wght@0,400;0,700;1,400&family=Pinyon+Script&family=Tinos&family=Arimo&display=swap">
<style>
  :root {
    --rose-deep: #b3137a;
    --rose-pill: #c21a80;
    --rose-mid: #eaa3c6;
    --rose-soft: #f6d3e3;
    --rose-pale: #fbe9f1;
    --leaf: #6f8f55;
    --band: rgba(255, 246, 250, 0.55);
    --band-low: rgba(255, 246, 250, 0.5);
    --white: #ffffff;
    --ink: #111111;
  }
  html, body {
    margin: 0;
    padding: 0;
    width: 1200px;
    height: 666px;
    overflow: hidden;
    background: var(--white);
  }
  .label {
    position: relative;
    width: 1200px;
    height: 666px;
    overflow: hidden;
    font-family: "EB Garamond", Georgia, serif;
    color: var(--rose-deep);
  }
  .rose-photo {
    position: absolute;
    inset: 0;
    background:
      radial-gradient(circle at 760px 500px, #f7dfa0 0, #f3c7cf 70px, transparent 180px),
      radial-gradient(ellipse at 700px 360px, var(--rose-pale) 0, var(--rose-soft) 260px, var(--rose-mid) 520px, transparent 700px),
      radial-gradient(circle at 1180px 40px, var(--leaf) 0, transparent 90px),
      radial-gradient(circle at 20px 120px, #8e7d86 0, transparent 140px),
      linear-gradient(160deg, #d98ab3 0%, var(--rose-mid) 40%, #f2bcd4 70%, #e58fbb 100%);
  }
  .band-main {
    position: absolute;
    left: 0;
    top: 146px;
    width: 1200px;
    height: 334px;
    background: var(--band);
  }
  .band-address {
    position: absolute;
    left: 284px;
    top: 520px;
    width: 916px;
    height: 112px;
    background: var(--band-low);
  }
  .brand-pill {
    position: absolute;
    left: 522px;
    top: 62px;
    width: 486px;
    height: 58px;
    border-radius: 20px;
    background: var(--rose-pill);
    color: var(--white);
    font-family: "Cinzel", "Times New Roman", serif;
    font-weight: 600;
    font-size: 40px;
    letter-spacing: 4px;
    display: flex;
    align-items: center;
    justify-content: center;
    margin: 0;
  }
  .info {
    position: absolute;
    left: 42px;
    top: 152px;
    width: 320px;
    font-family: "Tinos", "Times New Roman", serif;
    font-size: 21px;
    line-height: 33px;
    margin: 0;
  }
  .info p { margin: 0; }
  .best-before {
    position: absolute;
    left: 38px;
    top: 430px;
    font-family: "Tinos", "Times New Roman", serif;
    font-size: 24px;
    line-height: 32px;
    margin: 0;
  }
  .product-name {
    position: absolute;
    left: 460px;
    top: 212px;
    width: 700px;
    text-align: center;
    font-family: "Pinyon Script", cursive;
    font-weight: 400;
    font-size: 106px;
    line-height: 1;
    margin: 0;
  }
  .pitch {
    position: absolute;
    left: 418px;
    top: 326px;
    width: 680px;
    text-align: center;
    font-style: italic;
    font-size: 31px;
    line-height: 46px;
    margin: 0;
  }
  .weight {
    position: absolute;
    left: 1096px;
    top: 434px;
    font-family: "Tinos", "Times New Roman", serif;
    font-size: 26px;
    line-height: 32px;
    margin: 0;
  }
  .barcode-space {
    position: absolute;
    left: 41px;
    top: 481px;
    width: 238px;
    height: 152px;
    background: var(--white);
    border: 1.5px solid var(--ink);
    color: var(--ink);
    font-family: "Arimo", Arial, sans-serif;
    font-size: 26px;
    line-height: 34px;
    display: flex;
    align-items: center;
    justify-content: center;
    text-align: center;
  }
  .address {
    position: absolute;
    left: 430px;
    top: 538px;
    width: 700px;
    text-align: center;
    font-weight: 700;
    font-size: 26px;
    line-height: 38px;
    margin: 0;
    font-style: normal;
  }
</style>
</head>
<body>
  <main class="label">
    <div class="rose-photo" role="img" aria-label="Close-up photograph of a soft pink old-fashioned English rose in full bloom"></div>
    <div class="band-main"></div>
    <div class="band-address"></div>

    <h2 class="brand-pill">Meadow Crown</h2>

    <div class="info">
      <p>INGREDIENTS: Sugar, water,<br>rose petals, lemon juice,<br>natural jelling agent<br>(agar-agar)</p>
      <p>STORAGE: Store in a cool dry<br>place, once opened keep<br>refrigerated and consume<br>within 4 weeks.</p>
    </div>
    <p class="best-before">BEST BEFORE:&nbsp; See base</p>

    <h1 class="product-name">Rose Petal Jelly</h1>
    <p class="pitch">With whole petals - a taste of summer,<br>delicious on scones, as a filling in sponge cake,<br>as a topping on ice cream or yogurt.</p>
    <p class="weight">200g</p>

    <div class="barcode-space">BAR<br>CODE</div>

    <address class="address">MEADOW CROWN&nbsp; The Larches, Pardew Lane,<br>Ashcombe, Westmereshire&nbsp; GL17 4RX</address>
  </main>
</body>
</html>
```